KVB Website

We need a website for a company based in Doha Qatar called Brightpath Talent Global. It is a global recruitment company, that specializes in both mass recruitment and headhunting. The company is the number 1 one stop shop for recruitment in Qatar. It recruits from all over the world Europe, Asia, Americas, Middle East, Africa for Qatar.

Target Market(s)

Multinational companies, fortune 500 company CEO's, any top earning companies that are looking for a large number of employees or headhunting employees.
Also for candidates looking for companies to work in Qatar.

Industry/Entity Type

Shop

Colors
ffffff

Requirements
Must have
• Most important qualities the website needs to have:
Clean
Modern
Elegant
Professional
Less Tabs
Minimalisitc

Some examples, I would like you to follow are here:
http://www.velmora.ca/
http://www.trovenkip.com/
https://quelbrandix.com/match#

The main color should be white and it has to have a very stylish, modern and cool look. While being minimalistic. I do not want too many tabs. I want it to be simplistic to understand. the only place where the pink logo color is should be in the logo. The logo color should not be anywhere else. It has to be absolutely sleek. Please follow the example websites that I have provided.

I will send the contact details you need to add later. There is no need for a log in page.

Whatever you think that may be important for a recruitment site do suggest. But there is no need for a log in area as we are a different kind of recruitment company.

There should be an area for testimonials from clients. There should also be an area for news flash for the latest countries we are hiring from and the latest companies we are hiring for and the latest positions we are looking for.

Show me the best please. Whoever gives me the best, I will give them an order for the 2nd website too.

Nice to have
• I have included a powerpoint to explain more!

```html
<!DOCTYPE html>
<html lang="en">
<head>
<meta charset="utf-8">
<title>Brightpath Talent Global – Contact</title>
<link href="https://fonts.googleapis.com/css2?family=Zilla+Slab:wght@300;400;600;700&family=Roboto+Condensed:wght@700&display=swap" rel="stylesheet">
<style>
  :root {
    --page-bg: #fafafa;
    --header-bg: #ffffff;
    --panel-bg: #f2f2f2;
    --field-bg: #ffffff;
    --text-muted: #8c8c8c;
    --text-nav: #555555;
    --nav-marker: #6b6b6b;
    --brand: #a3245f;
    --header-shadow: rgba(0, 0, 0, 0.08);
  }

  * { box-sizing: border-box; margin: 0; padding: 0; }

  html, body {
    width: 1200px;
    height: 900px;
    overflow: hidden;
    background: var(--page-bg);
    font-family: "Zilla Slab", Georgia, serif;
  }

  .site-header {
    position: absolute;
    left: 0; top: 0;
    width: 1200px;
    height: 83px;
    background: var(--header-bg);
    box-shadow: 0 4px 14px var(--header-shadow);
    z-index: 2;
  }

  .brand {
    position: absolute;
    left: 114px;
    top: 26px;
    display: flex;
    align-items: center;
    gap: 10px;
  }

  .brand-mark {
    width: 16px;
    height: 16px;
    border-radius: 50%;
    background: var(--brand);
  }

  .brand-name {
    font-family: "Roboto Condensed", Arial, sans-serif;
    font-weight: 700;
    font-size: 25px;
    color: var(--brand);
    letter-spacing: 0.2px;
  }

  .main-nav {
    position: absolute;
    top: 38px;
    left: 0;
    width: 1200px;
  }

  .main-nav a {
    position: absolute;
    font-weight: 600;
    font-size: 19px;
    color: var(--text-nav);
    text-decoration: none;
  }

  .nav-home { left: 870px; }
  .nav-work { left: 976px; }
  .nav-contact { left: 1070px; }

  .nav-home, .nav-work, .nav-contact { display: none; }

  .nav-list { position: absolute; left: 798px; display: flex; gap: 0; }
  .nav-list a { position: static; display: block; }
  .nav-list a + a { margin-left: 52px; }

  .nav-list a.is-current::after {
    content: "";
    display: block;
    width: 70px;
    height: 7px;
    margin-top: 13px;
    background: var(--nav-marker);
  }

  .contact-section {
    position: absolute;
    top: 0; left: 0;
    width: 1200px;
    height: 900px;
  }

  .contact-card {
    position: absolute;
    top: 205px;
    width: 450px;
  }

  .contact-employers { left: 114px; }
  .contact-workers { left: 618px; }

  .contact-title {
    font-weight: 300;
    font-size: 23px;
    letter-spacing: 0.6px;
    color: var(--text-muted);
    text-transform: uppercase;
    margin-left: 2px;
    height: 30px;
  }

  .contact-form {
    background: var(--panel-bg);
    width: 450px;
    height: 560px;
    padding: 34px 27px 0 0;
    position: relative;
  }

  .form-row {
    display: flex;
    align-items: flex-start;
    margin-bottom: 23px;
  }

  .form-label {
    width: 172px;
    text-align: right;
    padding-right: 10px;
    font-weight: 300;
    font-size: 16px;
    color: var(--text-muted);
    line-height: 31px;
  }

  .form-field {
    width: 251px;
    height: 31px;
    border: none;
    background: var(--field-bg);
    font-family: inherit;
    font-size: 16px;
    color: var(--text-nav);
    padding: 0 8px;
  }

  .form-field.is-long {
    height: 318px;
    resize: none;
    margin-top: 4px;
  }

  .form-row.row-description .form-label { line-height: 22px; padding-top: 4px; }

  .send-button {
    position: absolute;
    right: 27px;
    top: 482px;
    width: 79px;
    height: 31px;
    border: none;
    background: var(--field-bg);
    font-family: inherit;
    font-weight: 600;
    font-size: 20px;
    letter-spacing: 1px;
    color: var(--text-muted);
  }
</style>
</head>
<body>
  <header class="site-header">
    <div class="brand">
      <span class="brand-mark"></span>
      <span class="brand-name">Brightpath Talent Global</span>
    </div>
    <nav class="main-nav">
      <div class="nav-list">
        <a href="#">Home</a>
        <a href="#">Work</a>
        <a href="#" class="is-current">Contact</a>
      </div>
    </nav>
  </header>

  <main class="contact-section">
    <section class="contact-card contact-employers">
      <h2 class="contact-title">Employers Contact</h2>
      <form class="contact-form">
        <div class="form-row">
          <label class="form-label" for="company-name">Company name:</label>
          <input class="form-field" id="company-name" type="text">
        </div>
        <div class="form-row">
          <label class="form-label" for="employer-title">Title:</label>
          <input class="form-field" id="employer-title" type="text">
        </div>
        <div class="form-row row-description">
          <label class="form-label" for="employer-description">Description:</label>
          <textarea class="form-field is-long" id="employer-description"></textarea>
        </div>
        <button class="send-button" type="button">SEND</button>
      </form>
    </section>

    <section class="contact-card contact-workers">
      <h2 class="contact-title">Workers Contact</h2>
      <form class="contact-form">
        <div class="form-row">
          <label class="form-label" for="worker-name">Your name:</label>
          <input class="form-field" id="worker-name" type="text">
        </div>
        <div class="form-row">
          <label class="form-label" for="worker-position">Position:</label>
          <input class="form-field" id="worker-position" type="text">
        </div>
        <div class="form-row row-description">
          <label class="form-label" for="worker-description">Description:</label>
          <textarea class="form-field is-long" id="worker-description"></textarea>
        </div>
        <button class="send-button" type="button">SEND</button>
      </form>
    </section>
  </main>
</body>
</html>
```